Social Media Graphics - Oakline Push REVISED

Create 6-7 individual social media graphics (square size) to encourage folks to join our online course called:

The Harvest Ledger Circle
How to Launch a Multi-Million Business From Scratch
Sign Up Today!

IMPORTANT: Make the largest and most prominent text on the graphic be: How to Launch a Multi-Million Business From Scratch

For the color scheme of the graphics, let's try a blue color palette; make sure the graphics appeal to both men and women

Make sure each graphic contains 1 of the 3 pics attached (crop pic as needed); and make sure one of the graphics is all TEXT only.

Target Market(s)

men and women looking to start a business

Industry/Entity Type

Entrepreneurship

Colors
0054AA
0677BA
7BADD7
CADEEF
E8F1F8

Requirements
Must have
• All the text and use the 3 pics provided; one graphic can be all text; Simple, modern design that's easy to read

```html
<!DOCTYPE html>
<html lang="en">
<head>
<meta charset="utf-8">
<title>The Harvest Ledger Circle – Sign Up Today</title>
<link href="https://fonts.googleapis.com/css2?family=Anton&family=Oswald:wght@600;700&display=swap" rel="stylesheet">
<style>
  :root {
    --sky-light: #1b93d2;
    --sky-mid: #16699e;
    --sky-deep: #0d4069;
    --navy-panel: #1f1f3d;
    --frame-line: #3a9ad9;
    --accent-blue: #3a9ad9;
    --white: #ffffff;
  }
  html, body {
    margin: 0;
    padding: 0;
    width: 1200px;
    height: 1200px;
    overflow: hidden;
    background: var(--sky-deep);
  }
  .social-graphic {
    display: block;
    width: 1200px;
    height: 1200px;
  }
  .course-name {
    font-family: "Oswald", "Arial Narrow", sans-serif;
    font-weight: 600;
    fill: var(--white);
  }
  .headline {
    font-family: "Anton", "Impact", sans-serif;
    fill: var(--white);
  }
  .call-to-action {
    font-family: "Oswald", "Arial Narrow", sans-serif;
    font-weight: 700;
    fill: var(--accent-blue);
  }
  .cta-rule {
    stroke: var(--accent-blue);
    stroke-width: 5;
  }
  .panel { fill: var(--navy-panel); }
  .panel-frame {
    fill: none;
    stroke: var(--frame-line);
    stroke-width: 1.6;
  }
</style>
</head>
<body>
<svg class="social-graphic" viewBox="0 0 1200 1200" xmlns="http://www.w3.org/2000/svg">
  <defs>
    <radialGradient id="sky-glow" cx="600" cy="90" r="760" gradientUnits="userSpaceOnUse">
      <stop offset="0" stop-color="var(--sky-light)"/>
      <stop offset="0.45" stop-color="var(--sky-mid)"/>
      <stop offset="1" stop-color="var(--sky-deep)"/>
    </radialGradient>
  </defs>

  <rect class="backdrop" x="0" y="0" width="1200" height="1200" fill="url(#sky-glow)"/>

  <g class="course-title">
    <text class="course-name" x="231" y="224" font-size="145" textLength="774" lengthAdjust="spacingAndGlyphs">THE HARVEST</text>
    <text class="course-name" x="248" y="370" font-size="145" textLength="742" lengthAdjust="spacingAndGlyphs">LEDGER CIRCLE</text>
  </g>

  <g class="headline-card">
    <rect class="panel" x="55" y="409" width="1091" height="616" rx="26"/>
    <rect class="panel-frame" x="70" y="426" width="1061" height="578" rx="36"/>
    <rect class="panel-frame" x="75" y="431" width="1051" height="568" rx="32"/>

    <text class="headline" x="118" y="631" font-size="200" textLength="950" lengthAdjust="spacingAndGlyphs">HOW TO LAUNCH</text>
    <text class="headline" x="118" y="814" font-size="189" textLength="952" lengthAdjust="spacingAndGlyphs">A MULTI-MILLION</text>
    <text class="headline" x="113" y="964" font-size="146" textLength="943" lengthAdjust="spacingAndGlyphs">BUSINESS FROM SCRATCH</text>
  </g>

  <g class="cta">
    <line class="cta-rule" x1="59" y1="1081" x2="430" y2="1081"/>
    <text class="call-to-action" x="452" y="1110" font-size="62" textLength="303" lengthAdjust="spacingAndGlyphs">SIGN UP TODAY</text>
    <line class="cta-rule" x1="770" y1="1081" x2="1140" y2="1081"/>
  </g>
</svg>
</body>
</html>
```